menu board design: rustle burger

we are a burger restaurant.
we need to re design our menu board to fit within the new design of the restaurant. we are after something simple and easy to read. the overall look and feel of the design should be inline with the design of the shop.

Target Market(s)

18-40 male and female

Colors

Designer to choose colors to be used in the design.

Requirements
Must have
• easy to read. good layout. white background. branding included in design.

```html
<!DOCTYPE html>
<html lang="en">
<head>
<meta charset="utf-8">
<title>Rustle Burger – Menu Board</title>
<link rel="stylesheet" href="https://fonts.googleapis.com/css2?family=Dosis:wght@400;500;600;700;800&family=Passion+One:wght@400;700&family=Josefin+Sans:wght@400&display=swap">
<style>
  :root {
    --blue: #1d4a93;
    --yellow: #e4b81c;
    --gold: #e2ac1f;
    --red: #b5232e;
    --ink: #3a3a3a;
    --paper: #f7f7f5;
    --pale: #f1e2a6;
  }
  * { margin: 0; padding: 0; box-sizing: border-box; }
  html, body { width: 1200px; height: 600px; overflow: hidden; background: var(--paper); }
  .board { position: relative; width: 1200px; height: 600px; background: var(--paper); font-family: "Dosis", sans-serif; color: var(--ink); }
  .abs { position: absolute; }

  .rule-v { position: absolute; width: 2px; background: var(--blue); }
  .rule-left { left: 24px; top: 24px; height: 556px; }
  .rule-right { left: 1172px; top: 100px; height: 405px; }

  .star-row { left: 185px; top: 32px; }
  .brand { left: 80px; top: 80px; width: 310px; text-align: center; font-family: "Dosis", sans-serif; font-weight: 800; color: var(--blue); font-size: 84px; line-height: 0.95; }
  .tagline { left: 80px; top: 323px; width: 310px; text-align: center; font-family: "Josefin Sans", sans-serif; font-size: 14px; letter-spacing: 5.4px; color: var(--blue); }
  .art { left: 70px; top: 340px; width: 290px; height: 222px; border-radius: 10px; background: radial-gradient(ellipse at 50% 55%, var(--pale) 0%, #f4ecd0 60%, rgba(247,247,245,0) 100%); }
  .deco { width: 40px; height: 40px; border-radius: 8px; background: #dbe3f0; }

  .banner { position: absolute; background: var(--yellow); font-family: "Passion One", sans-serif; text-align: center; line-height: 1; }
  .banner-lg { color: var(--blue); font-size: 29px; padding: 3px 0; }
  .banner-md { color: var(--red); font-size: 21px; padding: 4px 0; }
  .banner-sm { color: var(--blue); font-family: "Dosis", sans-serif; font-weight: 700; font-size: 11.5px; padding: 2px 0; }

  .column { position: absolute; top: 60px; width: 320px; }
  .intro { text-align: center; font-size: 11.4px; line-height: 1.27; margin: 0 0 10px; }
  .note { text-align: center; color: var(--blue); font-weight: 700; font-size: 11.8px; margin-bottom: 8px; }
  .item { margin-bottom: 11px; }
  .item-line { display: flex; align-items: baseline; color: var(--gold); font-weight: 700; font-size: 12px; }
  .item-line .dots { flex: 1; border-bottom: 1.5px dotted var(--gold); margin: 0 2px; }
  .item-desc { font-size: 10.2px; line-height: 1.25; color: var(--ink); }

  .dash { position: absolute; top: 362px; height: 0; border-top: 2px dashed var(--blue); }
  .label-blue { color: var(--blue); font-weight: 700; font-size: 12px; text-align: center; }

  .price-line { position: absolute; display: flex; align-items: baseline; color: var(--gold); font-weight: 700; font-size: 12px; }
  .price-line .dots { flex: 1; border-bottom: 1.5px dotted var(--gold); margin: 0 2px; }
  .price-line .price { font-weight: 500; }

  .options { left: 618px; top: 500px; width: 163px; color: var(--gold); font-size: 11px; line-height: 1.32; text-align: justify; }
  .options b { font-weight: 700; font-size: 12px; }
  .ribs-desc { left: 820px; top: 432px; width: 340px; text-align: center; font-size: 10.2px; line-height: 1.3; }
  .sauce { left: 1022px; top: 486px; color: var(--blue); font-weight: 700; font-size: 12px; line-height: 1.25; }
</style>
</head>
<body>
<main class="board">
  <div class="rule-v rule-left"></div>
  <div class="rule-v rule-right"></div>

  <svg class="abs star-row" width="112" height="20" viewBox="0 0 112 20" aria-hidden="true">
    <g fill="#1d4a93">
      <polygon transform="translate(8 10) scale(0.75)" points="0,-10 2.9,-3.1 9.5,-3.1 4.2,1.2 5.9,8.1 0,4 -5.9,8.1 -4.2,1.2 -9.5,-3.1 -2.9,-3.1"/>
      <polygon transform="translate(31 10) scale(0.75)" points="0,-10 2.9,-3.1 9.5,-3.1 4.2,1.2 5.9,8.1 0,4 -5.9,8.1 -4.2,1.2 -9.5,-3.1 -2.9,-3.1"/>
      <polygon transform="translate(56 9) scale(0.95)" points="0,-10 2.9,-3.1 9.5,-3.1 4.2,1.2 5.9,8.1 0,4 -5.9,8.1 -4.2,1.2 -9.5,-3.1 -2.9,-3.1"/>
      <polygon transform="translate(81 10) scale(0.75)" points="0,-10 2.9,-3.1 9.5,-3.1 4.2,1.2 5.9,8.1 0,4 -5.9,8.1 -4.2,1.2 -9.5,-3.1 -2.9,-3.1"/>
      <polygon transform="translate(104 10) scale(0.75)" points="0,-10 2.9,-3.1 9.5,-3.1 4.2,1.2 5.9,8.1 0,4 -5.9,8.1 -4.2,1.2 -9.5,-3.1 -2.9,-3.1"/>
    </g>
  </svg>

  <h1 class="abs brand">Rustle<br>Burger</h1>
  <p class="abs tagline">CLASSICS FOR A REASON</p>
  <div class="abs art" role="img" aria-label="Sketched drink glass and burger over a large pale yellow star"></div>

  <div class="abs deco" style="left:1142px;top:12px" role="img" aria-label="Sketched blue star"></div>
  <div class="abs deco" style="left:24px;top:556px" role="img" aria-label="Sketched blue star"></div>
  <div class="abs deco" style="left:1146px;top:556px" role="img" aria-label="Sketched blue star"></div>

  <div class="banner banner-lg" style="left:494px;top:24px;width:206px">BEEF BURGERS</div>
  <section class="column" style="left:438px">
    <p class="intro">All our patties are 100% natural beef. We know because we grind it ourselves, smashed to order on a hot grill rite in from of you</p>
    <p class="note">DOUBLE PATTY ADD 4</p>
    <div class="item"><div class="item-line"><span>CLASSIC BEEF</span><span class="dots"></span><span>8.9</span></div>
      <p class="item-desc">Shredded lettuce, sliced tomato, caramelised onions, beetroot and BBQ sauce on a buttered sesame seed bum.</p></div>
    <div class="item" style="margin-top:16px"><div class="item-line"><span>CHEESE BURGER</span><span class="dots"></span><span>9.5</span></div>
      <p class="item-desc">Dill pickles, minced onion, american cheese, mustard and ketchup on soft milk bun.</p></div>
    <div class="item"><div class="item-line"><span>FLAME GRILL</span><span class="dots"></span><span>9.5</span></div>
      <p class="item-desc">Shredded lettuce, sliced tomato, minced onion, dill pickles, american cheese, mayo and ketchup on a soft bun.</p></div>
    <div class="item"><div class="item-line"><span>BIG STACK</span><span class="dots"></span><span>9.9</span></div>
      <p class="item-desc">Shredded lettuce, dil pickles, minced onion, american cheese and special sauce on a soft milk bun.</p></div>
  </section>

  <div class="banner banner-lg" style="left:814px;top:26px;width:264px">CHICKEN BURGERS</div>
  <section class="column" style="left:806px">
    <p class="intro">All our patties are 100% natural beef. We know because we grind it ourselves, smashed to order on a hot grill rite in from of you</p>
    <p class="note">DOUBLE PATTY ADD 4</p>
    <div class="item"><div class="item-line"><span>CLASSIC BEEF</span><span class="dots"></span><span>8.9</span></div>
      <p class="item-desc">Shredded lettuce, sliced tomato, caramelised onions, beetroot and BBQ sauce on a buttered sesame seed bum.</p></div>
    <div class="item" style="margin-top:16px"><div class="item-line"><span>CHEESE BURGER</span><span class="dots"></span><span>9.5</span></div>
      <p class="item-desc">Dill pickles, minced onion, american cheese, mustard and ketchup on soft milk bun.</p></div>
    <div class="item"><div class="item-line"><span>FLAME GRILL</span><span class="dots"></span><span>9.5</span></div>
      <p class="item-desc">Shredded lettuce, sliced tomato, minced onion, dill pickles, american cheese, mayo and ketchup on a soft bun.</p></div>
    <div class="item"><div class="item-line"><span>TRUFFLED</span><span class="dots"></span><span>9.9</span></div>
      <p class="item-desc">Rocket, caramelised onion, dill pickles, havarti cheese and truffle infused mayo on a soft milk bun.</p></div>
  </section>

  <div class="dash" style="left:426px;width:262px"></div>
  <div class="dash" style="left:855px;width:276px"></div>
  <div class="banner banner-lg" style="left:707px;top:345px;width:136px;font-size:33px">SIDES</div>

  <div class="banner banner-md" style="left:462px;top:386px;width:228px">NACHOS &amp; LOADED FRIES</div>
  <div class="banner banner-sm" style="left:484px;top:443px;width:73px">STEP ONE</div>
  <div class="banner banner-sm" style="left:659px;top:443px;width:74px">STEP TWO</div>
  <p class="abs label-blue" style="left:450px;top:471px;width:142px">CHOOSE EITHER,</p>
  <p class="abs label-blue" style="left:630px;top:471px;width:140px">CHOOSE ONE,</p>

  <div class="price-line" style="left:432px;top:500px;width:180px"><span>SEASONED FRIES</span><span class="dots"></span><span class="price">9.9</span></div>
  <p class="abs" style="left:432px;top:529px;color:var(--gold);font-weight:700;font-size:12px">OR FRESHLY COOKED</p>
  <div class="price-line" style="left:432px;top:543px;width:180px"><span>CORN CHIPS</span><span class="dots"></span><span class="price">11.5</span></div>

  <p class="abs options"><b>GUACAMOLE</b> salsa fresca, guacamole, jalapeñoz, cheese sauce and sour cream. <b>BEEF CHILLI</b> salsa fresca, beef chilli, jalapeños, cheese sauce and sour cream.</p>

  <div class="banner banner-md" style="left:890px;top:385px;width:228px">BUFFALO CHICKEN RIBS</div>
  <p class="abs ribs-desc">Buffalo style fried chicken ribs smothered in one dur mouth-watering sauce. Served with a side of ranch sauce.</p>
  <div class="price-line" style="left:827px;top:486px;width:158px"><span>6 PACK</span><span class="dots"></span><span class="price">6.9</span></div>
  <div class="price-line" style="left:827px;top:515px;width:158px"><span>12 PACK</span><span class="dots"></span><span class="price">12.9</span></div>
  <div class="price-line" style="left:827px;top:544px;width:158px"><span>24 PACK</span><span class="dots"></span><span class="price">23.9</span></div>
  <p class="abs sauce">CLASSIC HOT SAUCE<br>OR SMOKY BBQ</p>

  <svg class="abs" style="left:1038px;top:520px" width="72" height="72" viewBox="0 0 72 72" aria-hidden="true">
    <circle cx="36" cy="36" r="32" fill="none" stroke="#1d4a93" stroke-width="2"/>
  </svg>
</main>
</body>
</html>
```